A clean crisp business card for a Landscape Construction company. Designed to be easy to read contact/ info and also be appealing/interesting, unlike a traditional business card.

Industry/Entity Type

Landscape Construction

Contact Information for Business Card

Company name : Brambleford Landscape Construction, phone number: (877) 62Vista, website:Bramblefordyards.example, Email, sales@bramblefordyards.example

Requirements
Nice to have
• Luxurious finishes/ details…. Icons or emblems next to contact info
Should not have
• Clipart or general pictures

```html
<!DOCTYPE html>
<html lang="en">
<head>
<meta charset="utf-8">
<title>Brambleford Landscape Construction – Business Card</title>
<link rel="stylesheet" href="https://fonts.googleapis.com/css2?family=Libre+Baskerville:wght@700&family=Arimo:wght@400&display=swap">
<style>
  :root {
    --backdrop: #141414;
    --card: #262626;
    --card-edge: #303030;
    --blue: #1f6fc4;
    --green: #8cc63f;
    --white: #f2f2f2;
    --emboss: #1c1c1c;
    --emboss-light: #333333;
  }
  * { margin: 0; padding: 0; box-sizing: border-box; }
  html, body {
    width: 1200px;
    height: 900px;
    overflow: hidden;
    background: var(--backdrop);
  }
  .sheet {
    width: 1200px;
    height: 900px;
    display: flex;
    flex-direction: column;
    align-items: center;
    justify-content: center;
    gap: 50px;
  }
  .card {
    width: 630px;
    height: 360px;
    background: var(--card);
    border: 1px solid var(--card-edge);
    border-radius: 22px;
    position: relative;
    box-shadow: 0 14px 30px rgba(0,0,0,0.55);
  }
  /* Front: contact side */
  .contact-block {
    position: absolute;
    left: 48px;
    top: 92px;
    width: 330px;
  }
  .person-name {
    font-family: "Libre Baskerville", serif;
    font-weight: 700;
    font-size: 28px;
    letter-spacing: 1px;
    line-height: 1;
  }
  .person-name .first { color: var(--blue); }
  .person-name .last { color: var(--green); }
  .person-role {
    font-family: "Arimo", sans-serif;
    font-size: 17px;
    color: var(--white);
    margin-top: 6px;
    margin-bottom: 16px;
  }
  .contact-list { list-style: none; }
  .contact-list li {
    display: flex;
    align-items: center;
    gap: 9px;
    font-family: "Arimo", sans-serif;
    font-size: 17px;
    color: var(--white);
    line-height: 1.55;
    white-space: nowrap;
  }
  .contact-list svg { width: 14px; height: 14px; flex: none; }
  .brand-front {
    position: absolute;
    right: 44px;
    top: 130px;
    width: 190px;
    display: flex;
    align-items: flex-start;
    justify-content: flex-end;
    gap: 10px;
  }
  .brand-mark {
    width: 14px;
    height: 14px;
    margin-top: 8px;
    border-radius: 50%;
    background: var(--green);
    flex: none;
  }
  .brand-name {
    font-family: "Libre Baskerville", serif;
    font-weight: 700;
    font-size: 20px;
    color: var(--blue);
    text-align: right;
    line-height: 1.35;
  }
  /* Back: tone-on-tone name */
  .card-back {
    display: flex;
    align-items: center;
    justify-content: center;
  }
  .brand-back {
    font-family: "Libre Baskerville", serif;
    font-weight: 700;
    font-size: 34px;
    color: var(--emboss);
    text-shadow: 0 1px 0 var(--emboss-light);
    text-align: center;
    line-height: 1.35;
  }
</style>
</head>
<body>
<main class="sheet">
  <section class="card card-front" aria-label="Card front">
    <div class="contact-block">
      <h1 class="person-name"><span class="first">OWEN</span> <span class="last">TALLIS</span></h1>
      <p class="person-role">Founder</p>
      <ul class="contact-list">
        <li>
          <svg viewBox="0 0 16 16" aria-hidden="true"><path fill="#8cc63f" d="M3.5 1.5l2.6 0 1 3.2-1.6 1.3a9 9 0 0 0 4.5 4.5l1.3-1.6 3.2 1v2.6c0 .8-.7 1.5-1.5 1.5A12 12 0 0 1 2 3c0-.8.7-1.5 1.5-1.5z"/></svg>
          (877) 62Vista
        </li>
        <li>
          <svg viewBox="0 0 16 16" aria-hidden="true"><rect x="1" y="3" width="14" height="10" rx="1.5" fill="#8cc63f"/><path d="M1.5 4l6.5 5 6.5-5" fill="none" stroke="#262626" stroke-width="1.4"/></svg>
          sales@bramblefordyards.example
        </li>
        <li>
          <svg viewBox="0 0 16 16" aria-hidden="true"><circle cx="8" cy="8" r="6.5" fill="none" stroke="#8cc63f" stroke-width="1.5"/><ellipse cx="8" cy="8" rx="2.8" ry="6.5" fill="none" stroke="#8cc63f" stroke-width="1.2"/><path d="M1.5 8h13" stroke="#8cc63f" stroke-width="1.2"/></svg>
          bramblefordyards.example
        </li>
      </ul>
    </div>
    <div class="brand-front">
      <span class="brand-mark" aria-hidden="true"></span>
      <p class="brand-name">Brambleford<br>Landscape<br>Construction</p>
    </div>
  </section>

  <section class="card card-back" aria-label="Card back">
    <p class="brand-back">Brambleford<br>Landscape Construction</p>
  </section>
</main>
</body>
</html>
```